Business Card For Halvenmoor Financial Consulting

Hi, I would like a business card designed. Bold, modern.
Please use the same design as the logo. I have also attached the website design to see the overall theme.
Wordmark Font
Color: Hex: #01AEF7

```html
<!DOCTYPE html>
<html lang="en">
<head>
<meta charset="utf-8">
<title>Halvenmoor Financial Consulting — Business Card</title>
<link rel="stylesheet" href="https://fonts.googleapis.com/css2?family=Montserrat:wght@400;500;700&family=Roboto:wght@400&display=swap">
<style>
  :root {
    --stage: #3b3b3b;
    --card: #19232d;
    --card-deep: #141d26;
    --pattern-light: #2a3a4a;
    --accent: #01aef7;
    --text: #e6ebef;
    --muted: #c3ccd4;
    --white: #ffffff;
  }
  * { box-sizing: border-box; margin: 0; padding: 0; }
  html, body { width: 1200px; height: 801px; overflow: hidden; }
  body {
    background: var(--stage);
    font-family: "Montserrat", sans-serif;
    position: relative;
  }
  .card {
    position: absolute;
    top: 257px;
    width: 500px;
    height: 286px;
    background: var(--card);
    border-bottom: 3px solid var(--accent);
    overflow: hidden;
  }
  .card--back { left: 60px; }
  .card--front { left: 640px; }

  /* back side */
  .identity {
    position: absolute;
    right: 270px;
    top: 118px;
    text-align: right;
  }
  .identity__name {
    color: var(--accent);
    font-weight: 700;
    font-size: 20px;
    letter-spacing: 0.5px;
  }
  .identity__title {
    color: var(--muted);
    font-family: "Roboto", sans-serif;
    font-size: 12px;
    margin-top: 2px;
  }
  .divider {
    position: absolute;
    left: 246px;
    top: 88px;
    width: 1.5px;
    height: 110px;
    background: var(--accent);
  }
  .contact {
    position: absolute;
    left: 262px;
    top: 92px;
    list-style: none;
    font-family: "Roboto", sans-serif;
    font-size: 11.5px;
    line-height: 20px;
    color: var(--text);
  }
  .contact__item { display: flex; align-items: center; gap: 6px; }
  .contact__icon { width: 10px; height: 10px; flex: none; }

  /* front side */
  .pattern {
    position: absolute;
    inset: 0;
    background: linear-gradient(135deg, var(--pattern-light) 0%, var(--card) 45%, var(--card-deep) 100%);
  }
  .brand {
    position: absolute;
    left: 50%;
    top: 50%;
    transform: translate(-50%, -50%);
    display: flex;
    align-items: center;
    gap: 12px;
    white-space: nowrap;
  }
  .brand__dot {
    width: 14px;
    height: 14px;
    border-radius: 50%;
    background: var(--accent);
    flex: none;
  }
  .brand__name {
    color: var(--white);
    font-weight: 700;
    font-size: 22px;
    letter-spacing: 1.5px;
    line-height: 1;
  }
</style>
</head>
<body>
  <section class="card card--back">
    <div class="identity">
      <p class="identity__name">MERRIT OSLANE</p>
      <p class="identity__title">President</p>
    </div>
    <div class="divider"></div>
    <ul class="contact">
      <li class="contact__item">1180 Larkspur Quay</li>
      <li class="contact__item">Bayridge CA 90412</li>
      <li class="contact__item">
        <svg class="contact__icon" viewBox="0 0 10 10"><path d="M2 0.5 L4 2.8 L3 4 Q4 6 6 7 L7.2 6 L9.5 8 L8 9.5 Q3.5 9 0.5 2 Z" fill="#01aef7"/></svg>
        555-014-2290
      </li>
      <li class="contact__item">
        <svg class="contact__icon" viewBox="0 0 10 10"><rect x="0.5" y="2" width="9" height="6.5" fill="#01aef7"/><path d="M0.5 2 L5 5.5 L9.5 2" fill="none" stroke="#19232d" stroke-width="1"/></svg>
        info@HalvenmoorConsulting.com
      </li>
      <li class="contact__item">
        <svg class="contact__icon" viewBox="0 0 10 10"><circle cx="5" cy="5" r="4.5" fill="#01aef7"/><path d="M0.5 5 H9.5 M5 0.5 Q2.5 5 5 9.5 M5 0.5 Q7.5 5 5 9.5" fill="none" stroke="#19232d" stroke-width="0.8"/></svg>
        www.HalvenmoorConsulting.com
      </li>
    </ul>
  </section>

  <section class="card card--front">
    <div class="pattern" role="img" aria-label="Embossed repeating decorative pattern in dark blue-grey tones"></div>
    <div class="brand">
      <span class="brand__dot"></span>
      <p class="brand__name">HALVENMOOR CONSULTING</p>
    </div>
  </section>
</body>
</html>
```